Business card design for Automotive workshop

We need a business card for a new automotive repair and tyre shop called Keelstone Prime Automotive located in New Zealand. We are a clean, modern and fresh workshop and company.

Front needs to feature logo,
my name:
Marlo Fenwicke (director)

Address:
48 Tarn Lane
Harrowvale 3592

Phone: 07 594 2713
Mobile: 027 451 9362
Email: office@keelstoneautomotive.example.nz
Website: keelstoneautomotive.example.nz

Back needs to feature an area to write down appointment details, date and time.

Also feature a list of jobs and work we do such as,
Vehicle Servicing
All Mechanical Repairs
Warrant of Fitness
Tyres & Wheel Alignments
Automotive Diagnostics
Automotive Parts & Supplies

```html
<!DOCTYPE html>
<html lang="en">
<head>
<meta charset="utf-8">
<title>Keelstone Prime Automotive – Business Card</title>
<link href="https://fonts.googleapis.com/css2?family=Open+Sans:wght@400;700&display=swap" rel="stylesheet">
<style>
  :root {
    --red: #e31e24;
    --black: #000000;
    --white: #ffffff;
    --page: #e9e7e4;
  }
  * { box-sizing: border-box; margin: 0; padding: 0; }
  html, body { width: 1200px; height: 1200px; overflow: hidden; background: var(--page); }
  body { position: relative; font-family: "Open Sans", Arial, sans-serif; color: var(--white); }

  .card {
    position: absolute;
    left: 267px;
    width: 670px;
    height: 390px;
    background: var(--red);
    padding: 22px;
  }
  .card--front { top: 166px; }
  .card--back { top: 606px; }
  .card__panel {
    position: relative;
    width: 100%;
    height: 100%;
    background: var(--black);
  }

  .brand-name {
    position: absolute;
    color: var(--red);
    font-weight: 700;
    text-transform: uppercase;
    text-align: right;
    line-height: 1.05;
  }
  .card--front .brand-name { right: 12px; top: 54px; font-size: 19px; letter-spacing: 1.5px; }
  .card--back .brand-name { right: 10px; top: 104px; font-size: 31px; letter-spacing: 2px; }

  .person { position: absolute; left: 28px; top: 133px; }
  .person__name { color: var(--red); font-weight: 700; font-size: 21px; letter-spacing: 0.6px; line-height: 1.1; }
  .person__role { font-size: 16px; letter-spacing: 0.5px; line-height: 1.3; }

  .contact { position: absolute; left: 28px; top: 207px; list-style: none; }
  .contact li { display: flex; align-items: center; height: 23.5px; font-size: 18px; letter-spacing: 0.4px; }
  .contact svg { width: 14px; height: 14px; margin-right: 10px; fill: var(--red); flex: none; }

  .services { position: absolute; left: 25px; top: 100px; list-style: none; }
  .services li { display: flex; align-items: center; height: 32px; font-size: 13px; letter-spacing: 0.5px; }
  .services li::before {
    content: ""; width: 5px; height: 5px; background: var(--red);
    border-radius: 1px; margin-right: 4px;
  }

  .appointment { position: absolute; display: flex; align-items: center; }
  .appointment__label { color: var(--red); font-size: 18px; letter-spacing: 0.4px; margin-right: 8px; }
  .appointment__field { width: 175px; height: 28px; background: var(--white); border-radius: 14px; }
  .appointment--date { left: 273px; top: 204px; }
  .appointment--time { left: 302px; top: 258px; }
</style>
</head>
<body>

<section class="card card--front">
  <div class="card__panel">
    <div class="brand-name">Keelstone Prime<br>Automotive</div>

    <div class="person">
      <div class="person__name">Marlo Fenwicke</div>
      <div class="person__role">Managing Director</div>
    </div>

    <ul class="contact">
      <li><svg viewBox="0 0 14 14"><path d="M3.5 0h7a1 1 0 0 1 1 1v12a1 1 0 0 1-1 1h-7a1 1 0 0 1-1-1V1a1 1 0 0 1 1-1zm.6 1.6v9.6h5.8V1.6zM7 11.8a.7.7 0 1 0 0 1.4.7.7 0 0 0 0-1.4z"/></svg>+ 027 451 9362</li>
      <li><svg viewBox="0 0 14 14"><path d="M0 5c2-3 12-3 14 0l-.4 2H11V5.5C9 5 5 5 3 5.5V7H.4zM3 8h8l2 5H1zm4 1.3a1.6 1.6 0 1 0 0 3.2 1.6 1.6 0 0 0 0-3.2z"/></svg>+ 07 594 2713</li>
      <li><svg viewBox="0 0 14 14"><path d="M0 2.5h14v1L7 8 0 3.5zm0 2.5 7 4.5L14 5v6.5H0z"/></svg>office@keelstoneautomotive.example.nz</li>
      <li><svg viewBox="0 0 14 14"><path d="M0 1.5h14v9H8.5v1.5H10v1H4v-1h1.5v-1.5H0zm1.2 1.2v6.6h11.6V2.7zM7 3.8a2 2 0 1 1 0 4 2 2 0 0 1 0-4z"/></svg>keelstoneautomotive.example.nz</li>
      <li><svg viewBox="0 0 14 14"><path d="M7 0a4.8 4.8 0 0 1 4.8 4.8C11.8 8.5 7 14 7 14S2.2 8.5 2.2 4.8A4.8 4.8 0 0 1 7 0zm0 3a1.8 1.8 0 1 0 0 3.6A1.8 1.8 0 0 0 7 3z"/></svg>48 Tarn Lane.Harrowvale 3592</li>
    </ul>
  </div>
</section>

<section class="card card--back">
  <div class="card__panel">
    <ul class="services">
      <li>Vehicle Servicing</li>
      <li>All Mechanical Repairs</li>
      <li>Warrant of Fitness</li>
      <li>Tyres &amp; Wheel Alignments</li>
      <li>Automotive Diagnostics</li>
      <li>Automotive Parts &amp; Supplies</li>
    </ul>

    <div class="brand-name">Keelstone Prime<br>Automotive</div>

    <div class="appointment appointment--date">
      <span class="appointment__label">Date</span>
      <span class="appointment__field"></span>
    </div>
    <div class="appointment appointment--time">
      <span class="appointment__label">Time</span>
      <span class="appointment__field"></span>
    </div>
  </div>
</section>

</body>
</html>
```